Residential Remodeling Contractor needs updated business card

I need a new design for my business card.
Name of the company is Ridgefell Construction. I need a card that commands presence, strength, integrity. I have been in business for 28 years. I am a Residential Remodeling Contractor that covers all aspects of a residential remodel and build.

```html
<!DOCTYPE html>
<html lang="en">
<head>
<meta charset="utf-8">
<title>Ridgefell Construction – Business Card</title>
<link href="https://fonts.googleapis.com/css2?family=Cinzel:wght@700&family=Arimo:wght@400&display=swap" rel="stylesheet">
<style>
  :root {
    --navy: #1b3d7d;
    --navy-deep: #1f3470;
    --ink: #333333;
    --paper: #ffffff;
    --backdrop: #9a9a9a;
  }
  * { margin: 0; padding: 0; box-sizing: border-box; }
  html, body { width: 1200px; height: 1059px; overflow: hidden; }
  body { background: var(--backdrop); position: relative; font-family: "Arimo", Arial, sans-serif; }

  .card {
    position: absolute;
    left: 256px;
    width: 690px;
    height: 392px;
    border-radius: 22px;
    overflow: hidden;
  }
  .card--front { top: 89px; background: var(--paper); }
  .card--back { top: 569px; background: var(--navy-deep); }

  .brand {
    position: absolute;
    display: flex;
    align-items: center;
    white-space: nowrap;
    font-family: "Arimo", Arial, sans-serif;
    font-weight: 400;
    line-height: 1;
  }
  .brand__mark { flex: none; }
  .card--front .brand { right: 40px; top: 112px; gap: 12px; color: var(--navy); font-size: 29px; }
  .card--front .brand__mark { width: 22px; height: 22px; background: var(--navy); }
  .card--back .brand { right: 60px; top: 300px; gap: 10px; color: var(--paper); font-size: 22px; }
  .card--back .brand__mark { width: 17px; height: 17px; background: var(--paper); }

  .person { position: absolute; left: 40px; top: 194px; }
  .person__name {
    font-family: "Cinzel", Georgia, serif;
    font-weight: 700;
    font-size: 23px;
    color: var(--navy);
    letter-spacing: 0.3px;
    line-height: 1.1;
  }
  .person__title { font-size: 16px; color: var(--ink); margin-top: 3px; }

  .divider {
    position: absolute; left: 40px; right: 40px; top: 254px;
    height: 1px; background: var(--navy);
  }

  .contacts { position: absolute; left: 40px; top: 268px; list-style: none; }
  .contacts li {
    display: flex; align-items: center; gap: 7px;
    font-size: 16.5px; color: var(--ink); height: 25px;
  }
  .contacts svg { width: 12px; height: 12px; fill: var(--navy); flex: none; }

  .address {
    position: absolute; right: 40px; top: 281px;
    text-align: right; font-size: 16.5px; color: var(--ink); line-height: 25px;
  }

  .footer-band { position: absolute; left: 0; bottom: 0; width: 690px; height: 40px; }
  .website {
    position: absolute; right: 20px; bottom: 11px;
    font-size: 16.5px; color: var(--paper);
  }

  .back-pattern { position: absolute; inset: 0; }
</style>
</head>
<body>

<section class="card card--front">
  <div class="brand"><span class="brand__mark"></span>Ridgefell Construction</div>

  <div class="person">
    <div class="person__name">OWEN HALVORSEN</div>
    <div class="person__title">Owner &amp; Manager</div>
  </div>

  <div class="divider"></div>

  <ul class="contacts">
    <li>
      <svg viewBox="0 0 12 12" aria-hidden="true"><path d="M1 4.5C1 3 3 2 6 2s5 1 5 2.5L9 5.5 8 4H4L3 5.5zM3 6h6l1 4.5H2z"/></svg>
      555 214 7780
    </li>
    <li>
      <svg viewBox="0 0 12 12" aria-hidden="true"><path d="M3 0.5h6a1 1 0 0 1 1 1v9a1 1 0 0 1-1 1H3a1 1 0 0 1-1-1v-9a1 1 0 0 1 1-1zM3.5 2v7h5V2zM6 9.6a.6.6 0 1 0 0 1.2.6.6 0 0 0 0-1.2z"/></svg>
      555-310-48265
    </li>
    <li>
      <svg viewBox="0 0 12 12" aria-hidden="true"><path d="M6 1l5.5 4v6H.5V5zM1.5 5.6v4.6L4.6 7.9zM10.5 5.6 7.4 7.9l3.1 2.3zM2.3 10.5h7.4L6 7.7z"/></svg>
      info@ridgefellconstruction.com
    </li>
  </ul>

  <div class="address">P.O. Box 418&nbsp; Alder Lane<br>Brookvale AB, T4R 2K9</div>

  <svg class="footer-band" viewBox="0 0 690 40" preserveAspectRatio="none" aria-hidden="true">
    <defs>
      <linearGradient id="fade-line" x1="0" x2="1" y1="0" y2="0">
        <stop offset="0" stop-color="#1b3d7d"/>
        <stop offset="0.7" stop-color="#1b3d7d" stop-opacity="0.8"/>
        <stop offset="1" stop-color="#1b3d7d" stop-opacity="0"/>
      </linearGradient>
    </defs>
    <rect x="0" y="13" width="395" height="4" fill="url(#fade-line)"/>
    <path d="M0 29 H365 C385 29 395 20 410 10 C420 3 428 0 445 0 H690 V40 H0 Z" fill="#1b3d7d"/>
  </svg>
  <div class="website">www.ridgefellconstruction.com</div>
</section>

<section class="card card--back">
  <svg class="back-pattern" viewBox="0 0 690 392" preserveAspectRatio="none" role="img" aria-label="Repeating pattern of brand motifs fading from deep navy to light blue">
    <defs>
      <linearGradient id="pattern-tone" x1="0" y1="1" x2="1" y2="0">
        <stop offset="0" stop-color="#1f3470"/>
        <stop offset="0.45" stop-color="#243d7c"/>
        <stop offset="1" stop-color="#5f80bd"/>
      </linearGradient>
    </defs>
    <rect width="690" height="392" fill="url(#pattern-tone)"/>
  </svg>
  <div class="brand"><span class="brand__mark"></span>Ridgefell Construction</div>
</section>

</body>
</html>
```